Letterhead and matching envelope design for a dental office

We need a new stationary design, letterhead and envelope #10, for a dental office in Denver area. We are called Bright Harbor Dental. We want a simple and minimalistic design but not a boring design. I wish to have one good point that makes it look professional. I have attached our logo. Feel free to use either one. I want the design for letterhead and envelope look like a "matching pair" but not look the same. The envelope doesn't have to be white and it will have an address window on bottom left.

Target Market(s)

everyone who visits dentist (adults)

Industry/Entity Type

Dental

Font styles to use
Other font styles liked:
• close to font on logo or something that matches well

Requirements
Must have
• professional
• simple, minimalistic
• unique point that stands out
Nice to have
• matching but not same design for letterhead and envelope
Should not have
• not look like all the other boring designs
• no flowery, distracting feats

```html
<!DOCTYPE html>
<html lang="en">
<head>
<meta charset="utf-8">
<title>Bright Harbor Dental – Letterhead</title>
<link href="https://fonts.googleapis.com/css2?family=Arimo:wght@400;700&family=Open+Sans:wght@400&display=swap" rel="stylesheet">
<style>
  :root {
    --backdrop: #ecebe8;
    --paper: #ffffff;
    --brand-green: #3bb54a;
    --wave-pale: #dcefd9;
    --text-gray: #7a7a7a;
    --heading-gray: #555555;
  }
  * { margin: 0; padding: 0; box-sizing: border-box; }
  html, body {
    width: 1112px; height: 1200px; overflow: hidden;
    background: var(--backdrop);
  }
  .letterhead {
    position: absolute; left: 215px; top: 88px;
    width: 697px; height: 985px;
    background: var(--paper);
    box-shadow: 0 2px 10px rgba(0,0,0,.15);
    overflow: hidden;
  }
  .brand {
    position: absolute; top: 60px; left: 0; width: 100%;
    display: flex; align-items: center; justify-content: center; gap: 10px;
  }
  .brand-dot {
    width: 14px; height: 14px; border-radius: 50%;
    background: var(--brand-green);
  }
  .brand-name {
    font-family: "Arimo", Arial, sans-serif; font-weight: 700;
    font-size: 20px; letter-spacing: 2px; text-transform: uppercase;
    color: var(--brand-green);
  }
  .letter-body {
    position: absolute; left: 61px; top: 366px; width: 575px;
    font-family: "Arimo", Arial, sans-serif;
  }
  .salutation {
    font-weight: 700; font-size: 15px; color: var(--heading-gray);
    margin-bottom: 19px;
  }
  .letter-body p.copy {
    font-size: 14.3px; line-height: 17px; color: var(--text-gray);
    text-align: justify; margin-bottom: 17px;
  }
  .signature {
    position: absolute; left: 62px; top: 712px; width: 132px; height: 64px;
    background: linear-gradient(90deg, #e6e6e6, #f4f4f4);
    border-radius: 4px;
  }
  .footer-accent {
    position: absolute; left: 0; top: 840px; width: 697px; height: 42px;
    background: linear-gradient(180deg, var(--paper), var(--wave-pale));
  }
  .footer-band {
    position: absolute; left: 0; top: 882px; width: 697px; height: 103px;
    background: var(--brand-green);
  }
  .contact-list {
    position: absolute; left: 61px; top: 896px; list-style: none;
    font-family: "Open Sans", Arial, sans-serif; font-size: 13.5px;
    color: #ffffff;
  }
  .contact-list li {
    display: flex; align-items: center; gap: 8px; height: 19px;
  }
  .contact-icon { width: 15px; height: 15px; flex: none; }
</style>
</head>
<body>
  <main class="letterhead">
    <header class="brand">
      <span class="brand-dot"></span>
      <span class="brand-name">Bright Harbor Dental</span>
    </header>

    <section class="letter-body">
      <p class="salutation">Dear Mr. Carter,</p>
      <p class="copy">Lorem Ipsum is simply dummy text of the printing and typesetting industry. Lorem Ipsum has been the industry's standard dummy text ever since the 1500s, when an unknown printer took a galley of type and scrambled it to make a type specimen book. It has survived not only five centuries, but also the leap into electronic typesetting, remaining essentially unchanged.</p>
      <p class="copy">The standard chunk of Lorem Ipsum used since the 1500s is reproduced below for those interested. Sections 1.10.32 and 1.10.33 from "de Finibus Bonorum et Malorum" by Cyrus are also reproduced in their exact original form, accompanied by English versions from the 1914 translation by H. Merrow</p>
      <p class="copy">Lorem Ipsum is simply dummy text of the printing and typesetting industry. Lorem Ipsum has been the industry's standard dummy text ever since the 1500s, when an unknown printer took a galley of type and scrambled it to make a type specimen book. It has survived not only five centuries, but also the leap into electronic typesetting, remaining essentially unchanged. It was popularised in the</p>
    </section>

    <div class="signature" role="img" aria-label="Handwritten signature of the sender"></div>

    <div class="footer-accent" role="img" aria-label="Soft green decorative accent above the footer"></div>
    <div class="footer-band"></div>

    <ul class="contact-list">
      <li>
        <svg class="contact-icon" viewBox="0 0 16 16"><circle cx="8" cy="8" r="8" fill="#fff"/><path d="M5.2 4.2l1.6-.3.8 2-1 .8c.5 1.1 1.3 1.9 2.4 2.4l.8-1 2 .8-.3 1.6c-3.4.2-6.5-2.9-6.3-6.3z" fill="var(--brand-green)"/></svg>
        720-555-0142
      </li>
      <li>
        <svg class="contact-icon" viewBox="0 0 16 16"><circle cx="8" cy="8" r="8" fill="#fff"/><rect x="4" y="5" width="8" height="6" rx="1" fill="var(--brand-green)"/><path d="M4.3 5.4L8 8.3l3.7-2.9" stroke="#fff" stroke-width="1" fill="none"/></svg>
        info@brightharbordental.com
      </li>
      <li>
        <svg class="contact-icon" viewBox="0 0 16 16"><circle cx="8" cy="8" r="8" fill="#fff"/><circle cx="8" cy="8" r="4.5" fill="none" stroke="var(--brand-green)" stroke-width="1"/><path d="M3.5 8h9M8 3.5c-2 2.5-2 6.5 0 9M8 3.5c2 2.5 2 6.5 0 9" stroke="var(--brand-green)" stroke-width="1" fill="none"/></svg>
        www.brightharbordental.com
      </li>
      <li>
        <svg class="contact-icon" viewBox="0 0 16 16"><circle cx="8" cy="8" r="8" fill="#fff"/><path d="M8 3.5a3 3 0 0 1 3 3c0 2.2-3 5.8-3 5.8S5 8.7 5 6.5a3 3 0 0 1 3-3z" fill="var(--brand-green)"/><circle cx="8" cy="6.5" r="1.1" fill="#fff"/></svg>
        4820 Maple Ridge Ave,Suite 210 Westminster, CO 80031
      </li>
    </ul>
  </main>
</body>
</html>
```